Corporate Business Card

Very professional, Modern, Not to busy, include phone address email, website
(253) 617-4930, 18761 52nd Avenue S, Kent, WA 98047, martin@plumlinegroup.com, varkoworks.com

Target Market(s)

Manufacturing

Industry/Entity Type

Aero, machining, manufacturing, Off road racing

Contact Information for Business Card

Phone, address email, website

```html
<!DOCTYPE html>
<html lang="en">
<head>
<meta charset="utf-8">
<title>Varko Works – Business Card</title>
<link href="https://fonts.googleapis.com/css2?family=Roboto:wght@400;700;900&family=Rajdhani:wght@700&display=swap" rel="stylesheet">
<style>
  :root {
    --navy: #263769;
    --navy-deep: #22315f;
    --red: #c32026;
    --backdrop: #2a2a2a;
    --white: #ffffff;
    --ink: #25356a;
  }
  * { margin: 0; padding: 0; box-sizing: border-box; }
  html, body { width: 1200px; height: 1138px; overflow: hidden; }
  body {
    background: var(--backdrop);
    font-family: "Roboto", Arial, sans-serif;
    position: relative;
  }
  .card {
    position: absolute;
    border-radius: 16px;
    overflow: hidden;
  }
  .card-front {
    left: 274px; top: 186px; width: 623px; height: 376px;
    background: linear-gradient(180deg, var(--navy) 0%, var(--navy-deep) 100%);
  }
  .front-name {
    position: absolute;
    left: 0; right: 0; top: 118px;
    text-align: center;
    color: var(--white);
    font-weight: 900;
    font-size: 62px;
    line-height: 72px;
    letter-spacing: 1px;
    text-transform: uppercase;
  }
  .front-rule {
    position: absolute;
    left: 106px; top: 211px;
    width: 196px; height: 3px;
    background: var(--white);
  }
  .front-web {
    position: absolute;
    left: 0; right: 0; top: 328px;
    text-align: center;
    color: var(--white);
    font-size: 15px;
    letter-spacing: 0.85em;
    padding-left: 0.85em;
  }
  .front-web .accent { color: var(--red); }

  .card-back {
    left: 276px; top: 608px; width: 619px; height: 374px;
    background: linear-gradient(180deg, #f4f4f4 0%, #e4e4e4 100%);
  }
  .back-name {
    position: absolute;
    left: 52px; top: 62px;
    color: var(--ink);
    font-weight: 900;
    font-size: 40px;
    line-height: 48px;
    text-transform: uppercase;
  }
  .back-rule {
    position: absolute;
    left: 48px; top: 126px;
    width: 120px; height: 2px;
    background: var(--ink);
  }
  .person {
    position: absolute;
    right: 46px; top: 74px;
    text-align: right;
    font-family: "Rajdhani", "Roboto", sans-serif;
    font-weight: 700;
    font-size: 30px;
    line-height: 25px;
    text-transform: uppercase;
  }
  .person .first { color: var(--ink); display: block; }
  .person .last { color: var(--red); display: block; }
  .contacts {
    position: absolute;
    left: 46px; top: 176px;
    list-style: none;
  }
  .contacts li {
    display: flex; align-items: center;
    height: 24.5px;
    color: var(--ink);
    font-size: 16px;
  }
  .contacts svg { width: 14px; height: 14px; margin-right: 19px; flex: none; }
  .footer-band {
    position: absolute;
    left: 0; right: 0; bottom: 0;
    height: 112px;
    background: var(--navy);
    border-top: 6px solid var(--red);
  }
  .address {
    position: absolute;
    right: 42px; top: 293px;
    text-align: right;
    color: #e9ecf4;
    font-size: 16px;
    font-style: normal;
    line-height: 24.5px;
  }
</style>
</head>
<body>
  <section class="card card-front">
    <div class="front-name">Varko Works</div>
    <div class="front-rule"></div>
    <div class="front-web">www.varko<span class="accent">works</span>.com</div>
  </section>

  <section class="card card-back">
    <div class="footer-band"></div>

    <div class="back-name">Varko Works</div>
    <div class="back-rule"></div>

    <div class="person"><span class="first">Martin</span><span class="last">Hale</span></div>

    <ul class="contacts">
      <li>
        <svg viewBox="0 0 14 14" aria-hidden="true"><path fill="var(--red)" d="M1 5 C1 2 13 2 13 5 L11 6 L10 4.5 L4 4.5 L3 6 Z M3 7 L11 7 L12.5 12 L1.5 12 Z"/></svg>
        (253) 617-4930
      </li>
      <li>
        <svg viewBox="0 0 14 14" aria-hidden="true"><rect x="0.5" y="3" width="13" height="9" fill="var(--red)"/><path d="M0.5 3 L7 8 L13.5 3" stroke="#fff" stroke-width="1.2" fill="none"/></svg>
        martin@plumlinegroup.com
      </li>
      <li>
        <svg viewBox="0 0 14 14" aria-hidden="true"><circle cx="7" cy="7" r="6" fill="var(--red)"/><path d="M1 7 H13 M7 1 V13 M7 1 C3 4 3 10 7 13 M7 1 C11 4 11 10 7 13" stroke="#fff" stroke-width="0.9" fill="none"/></svg>
        www.varkoworks.com
      </li>
    </ul>

    <address class="address">18761 52nd Avenue<br>S, Kent, WA 98047</address>
  </section>
</body>
</html>
```